Business Card Design

I already have a company logo for my company. I have a logo for the manufacturer we represent. I want a professional business card design.

```html
<!DOCTYPE html>
<html lang="en">
<head>
<meta charset="utf-8">
<title>Beacon Signal Co – Business Card</title>
<link href="https://fonts.googleapis.com/css2?family=Montserrat:wght@400;500;700&display=swap" rel="stylesheet">
<style>
  :root {
    --bg: #ecebe8;
    --gold-light: #a38a1f;
    --gold-mid: #8a7a3a;
    --gold-dark: #4f4a42;
    --accent-red: #e8414f;
    --accent-yellow: #e0b41c;
    --ink: #2b2b2b;
    --paper: #ffffff;
    --brand-light: #f4f4f4;
  }
  * { box-sizing: border-box; margin: 0; padding: 0; }
  html, body { width: 1200px; height: 913px; overflow: hidden; }
  body {
    background: var(--bg);
    font-family: "Montserrat", sans-serif;
    position: relative;
  }
  .card {
    position: absolute;
    top: 306px;
    width: 525px;
    height: 300px;
    border-radius: 4px;
    box-shadow: 0 10px 24px rgba(0,0,0,0.18);
    overflow: hidden;
  }
  .card-front {
    left: 50px;
    background: linear-gradient(135deg, var(--gold-light) 0%, var(--gold-mid) 50%, var(--gold-dark) 100%);
    display: flex;
    align-items: center;
    justify-content: center;
  }
  .brand {
    display: flex;
    align-items: center;
    gap: 14px;
  }
  .brand-mark {
    width: 34px;
    height: 34px;
    border-radius: 50%;
  }
  .brand-name {
    font-weight: 700;
    letter-spacing: 0.04em;
    text-transform: uppercase;
  }
  .card-front .brand-mark { background: var(--accent-red); }
  .card-front .brand-name { color: var(--brand-light); font-size: 34px; }

  .card-back {
    left: 625px;
    background: var(--paper);
    border-bottom: 8px solid var(--accent-yellow);
  }
  .card-back .brand {
    position: absolute;
    top: 26px;
    right: 26px;
    gap: 8px;
  }
  .card-back .brand-mark { width: 16px; height: 16px; background: var(--accent-yellow); }
  .card-back .brand-name { color: var(--accent-red); font-size: 17px; }

  .person { position: absolute; left: 30px; top: 112px; }
  .person-name { color: var(--accent-red); font-weight: 700; font-size: 20px; }
  .person-title { color: var(--ink); font-size: 12px; margin-top: 3px; }

  .address {
    position: absolute;
    right: 30px;
    top: 112px;
    text-align: right;
    color: var(--ink);
    font-size: 12px;
    line-height: 1.5;
  }
  .contact-list {
    position: absolute;
    left: 30px;
    bottom: 24px;
    list-style: none;
    color: var(--ink);
    font-size: 12.5px;
    line-height: 1.65;
  }
  .contact-list li { display: flex; align-items: center; gap: 10px; }
  .contact-list svg { width: 11px; height: 11px; fill: var(--accent-red); flex: none; }
</style>
</head>
<body>
  <section class="card card-front" aria-label="Card front">
    <div class="brand">
      <span class="brand-mark"></span>
      <span class="brand-name">Beacon Signal Co</span>
    </div>
  </section>

  <section class="card card-back" aria-label="Card back">
    <div class="brand">
      <span class="brand-mark"></span>
      <span class="brand-name">Beacon Signal Co</span>
    </div>

    <div class="person">
      <p class="person-name">Mark Ellison</p>
      <p class="person-title">Managing Director</p>
    </div>

    <p class="address">2480 Alder Ave<br>Denver, CO 80205</p>

    <ul class="contact-list">
      <li>
        <svg viewBox="0 0 24 24" aria-hidden="true"><path d="M6.6 10.8a15.1 15.1 0 0 0 6.6 6.6l2.2-2.2a1 1 0 0 1 1-.25 11.4 11.4 0 0 0 3.6.57 1 1 0 0 1 1 1V20a1 1 0 0 1-1 1A17 17 0 0 1 3 4a1 1 0 0 1 1-1h3.5a1 1 0 0 1 1 1c0 1.25.2 2.45.57 3.57a1 1 0 0 1-.25 1z"/></svg>
        555.210.0147
      </li>
      <li>
        <svg viewBox="0 0 24 24" aria-hidden="true"><path d="M2 5h20v14H2z M2 5l10 8 10-8" /></svg>
        info@beaconsignalco.com
      </li>
      <li>
        <svg viewBox="0 0 24 24" aria-hidden="true"><circle cx="12" cy="12" r="10"/></svg>
        www.beaconsignalco.com
      </li>
    </ul>
  </section>
</body>
</html>
```